Quorimo Business Card Design Project

We need a business card design for quorimo.example a company based in Berlin, Germany.

?Quorimo is marketplace that enables people all over the world to monetize and exchange their individual knowledge and language skills through interactive video sessions. User are matched by their interests.

On Quorimo everybody can be student or teacher (seller or buyer).

We would love to see designs that use or main color blue and green. The design should communicate what Quorimo enables - see my notice above.

Looking so forward to your designs
Cheers from Berlin,
Lorenz

Target Market(s)

globally

Industry/Entity Type

Teacher

Requirements
Must have
• Lorenz Hubeck
CEO
Quorimo.example

Quorimo e-Services GmbH
Lindenweg 87
10247 Berlin

Fon: +49 30 418 906 25 17
Mobile: 49 172 54 91 37 6
E-Mail: l.hubeck@quorimo.example
Web: www.quorimo.example

```html
<!DOCTYPE html>
<html lang="en">
<head>
<meta charset="utf-8">
<title>Quorimo business card</title>
<link rel="stylesheet" href="https://fonts.googleapis.com/css2?family=Open+Sans:wght@400;600;700&display=swap">
<style>
  :root {
    --backdrop: #1c1c1c;
    --card: #ffffff;
    --brand-blue: #1ba0dc;
    --brand-green: #8dc13f;
    --brand-grey: #6b6b6b;
    --text-blue: #1d95d2;
  }
  * { box-sizing: border-box; margin: 0; padding: 0; }
  html, body {
    width: 1200px; height: 900px; overflow: hidden;
    background: var(--backdrop);
    font-family: "Open Sans", Arial, sans-serif;
  }
  .stage {
    width: 1200px; height: 900px;
    display: flex; align-items: center; justify-content: center; gap: 50px;
  }
  .card {
    position: relative;
    width: 525px; height: 300px;
    background: var(--card);
    border-radius: 22px;
    overflow: hidden;
  }
  .wordmark {
    display: flex; align-items: center; gap: 12px;
  }
  .wordmark__square {
    width: 30px; height: 30px; background: var(--brand-blue);
  }
  .wordmark__name {
    font-size: 58px; font-weight: 400; line-height: 1;
    color: var(--brand-grey); letter-spacing: 0.5px;
  }

  /* front */
  .card--front .wordmark-block { position: absolute; left: 38px; top: 44px; }
  .person { position: absolute; left: 40px; top: 158px; }
  .person__name { color: var(--text-blue); font-weight: 700; font-size: 19px; }
  .person__role { color: var(--brand-green); font-weight: 700; font-size: 12px; margin-top: 2px; }
  .address {
    position: absolute; left: 40px; top: 212px;
    display: flex; gap: 6px;
    color: var(--text-blue); font-size: 13px; line-height: 1.4;
  }
  .address svg { margin-top: 3px; flex: none; }
  .contact {
    position: absolute; left: 320px; top: 178px;
    list-style: none; color: var(--text-blue); font-size: 12px; line-height: 1.55;
  }
  .contact li { display: flex; align-items: center; gap: 7px; }
  .contact svg { flex: none; }
  .edge-band {
    position: absolute; left: 0; right: 0; bottom: 0; height: 24px;
    background: var(--brand-blue);
  }
  .edge-band__accent {
    position: absolute; right: 0; top: 0; bottom: 0; width: 52px;
    background: var(--brand-green);
  }

  /* back */
  .card--back { display: flex; align-items: center; justify-content: center; }
  .card--back .web {
    color: var(--brand-green); font-weight: 600; font-size: 15px;
    margin: 10px 0 0 42px;
  }
</style>
</head>
<body>
<main class="stage">
  <section class="card card--front" aria-label="Card front">
    <div class="wordmark-block">
      <div class="wordmark">
        <span class="wordmark__square"></span>
        <span class="wordmark__name">quorimo</span>
      </div>
    </div>

    <div class="person">
      <p class="person__name">Lorenz Hubeck</p>
      <p class="person__role">CEO</p>
    </div>

    <div class="address">
      <svg width="12" height="11" viewBox="0 0 12 11" aria-hidden="true">
        <path d="M6 0 L12 5.5 H10 V11 H7.3 V7.5 H4.7 V11 H2 V5.5 H0 Z" fill="var(--brand-green)"/>
      </svg>
      <p>Quorimo e-Services GmbH<br>Lindenweg 87<br>10247 Berlin</p>
    </div>

    <ul class="contact">
      <li>
        <svg width="10" height="10" viewBox="0 0 10 10" aria-hidden="true">
          <path d="M2 0.5 L4 2.8 L3 4 Q4.5 6 6 7 L7.2 6 L9.5 8 L8.2 9.5 Q4 9 0.5 1.8 Z" fill="var(--brand-green)"/>
        </svg>
        +49 30 418 906 25 17
      </li>
      <li>
        <svg width="10" height="10" viewBox="0 0 10 10" aria-hidden="true">
          <rect x="2" y="0.5" width="6" height="9" rx="1" fill="none" stroke="var(--brand-green)" stroke-width="1.2"/>
        </svg>
        49 172 54 91 37 6
      </li>
      <li>
        <svg width="10" height="10" viewBox="0 0 10 10" aria-hidden="true">
          <rect x="0.5" y="2" width="9" height="6.5" fill="var(--brand-green)"/>
          <path d="M0.5 2 L5 5.5 L9.5 2" fill="none" stroke="#fff" stroke-width="0.9"/>
        </svg>
        l.hubeck@quorimo.example
      </li>
    </ul>

    <div class="edge-band"><span class="edge-band__accent"></span></div>
  </section>

  <section class="card card--back" aria-label="Card back">
    <div class="wordmark-block">
      <div class="wordmark">
        <span class="wordmark__square"></span>
        <span class="wordmark__name">quorimo</span>
      </div>
      <p class="web">www.quorimo.example</p>
    </div>
  </section>
</main>
</body>
</html>
```